Modern HomePage Design for Church

We are looking for a modern homepage design using the sections we put together in the template. The colors we want are blue, black, grey, and white. We do not want use the colors in the logo. Please modify the logo color to match the website color scheme.

Target Market(s)

Church

Industry/Entity Type

Church

Number of Pages Required

1 page

Colors
0293ce
ffffff
474747
9d9d9d

```html
<!DOCTYPE html>
<html lang="en">
<head>
<meta charset="utf-8">
<title>Wellspring of Grace Church</title>
<link href="https://fonts.googleapis.com/css2?family=Montserrat:wght@400;500;600;700&family=Open+Sans:wght@400;600&family=Dancing+Script:wght@600&display=swap" rel="stylesheet">
<style>
:root{
  --indigo:#22106b;
  --indigo-deep:#1b0b58;
  --royal:#1d1a8f;
  --ink:#111111;
  --charcoal:#2b2b2b;
  --grey:#474747;
  --mist:#9d9d9d;
  --paper:#efefef;
  --white:#ffffff;
  --sky:#0293ce;
}
*{margin:0;padding:0;box-sizing:border-box}
html,body{width:1200px;height:4327px;overflow:hidden}
body{font-family:"Open Sans",Arial,sans-serif;color:var(--grey);background:var(--white);position:relative}
section,header,footer{position:absolute;left:0;width:1200px;overflow:hidden}
.abs{position:absolute}
.head{font-family:"Montserrat",Arial,sans-serif;font-weight:700;text-transform:uppercase}
.btn{position:absolute;display:flex;align-items:center;justify-content:center;font-family:"Montserrat",Arial,sans-serif;font-weight:700;font-size:14px;text-transform:uppercase;letter-spacing:.5px}
.btn-solid{background:var(--royal);color:var(--white)}
.btn-line{border:2px solid var(--royal);color:var(--royal);background:var(--white)}
.btn-ghost{border:2px solid var(--white);color:var(--white)}
.copy{font-size:13.5px;line-height:26px}
.ph{position:absolute}

/* hero */
.hero{top:0;height:744px;background:linear-gradient(180deg,#2a2a3a 0%,#5a4a5a 35%,#b5705a 62%,#3a2a2e 100%)}
.hero .ph{inset:0}
.nav{position:absolute;top:0;left:0;width:1200px;height:58px;background:rgba(20,12,60,.85)}
.nav a{position:absolute;top:20px;color:var(--white);font-family:"Montserrat",Arial,sans-serif;font-weight:700;font-size:13px;text-decoration:none;text-transform:uppercase}
.brand{left:110px;top:92px;width:200px;color:var(--white);font-family:"Montserrat",Arial,sans-serif;font-weight:600;font-size:24px;line-height:28px;text-align:center;text-transform:uppercase}
.brand .dot{display:block;width:26px;height:26px;border-radius:50%;background:var(--white);margin:0 auto 8px}
.worship{left:880px;top:95px;width:208px;height:42px;font-size:13px}
.hero-title{left:0;width:1200px;text-align:center;color:var(--white)}
.hero-sub{top:470px;left:0;width:1200px;text-align:center;color:var(--white);font-family:"Montserrat",Arial,sans-serif;font-weight:500;font-size:21px;line-height:37px;text-transform:uppercase}

/* band */
.band{top:744px;height:70px;background:var(--indigo)}
.band p{left:167px;top:23px;color:var(--white);font-family:"Montserrat",Arial,sans-serif;font-weight:700;font-size:17px;text-transform:uppercase}

/* welcome */
.welcome{top:814px;height:508px;background:var(--white)}
.welcome .ph{left:640px;top:36px;width:560px;height:472px;background:linear-gradient(90deg,#f4f2f0,#d9cfc6 40%,#2a2522 75%,#e9e6e3)}
.signature{left:110px;top:426px;font-family:"Dancing Script",cursive;font-weight:600;font-size:32px;color:var(--indigo)}

/* meeting */
.meeting{top:1322px;height:279px;background:linear-gradient(90deg,#3a3a3a,#2a2a2a 50%,#3c3c3c)}
.count{top:88px;width:80px;text-align:center;color:var(--white)}
.count b{display:block;font-family:"Montserrat",Arial,sans-serif;font-size:24px}
.count span{font-size:11px}
.sep{top:92px;width:1px;height:60px;background:rgba(255,255,255,.35)}

/* beliefs */
.beliefs{top:1601px;height:384px;background:linear-gradient(180deg,#f4f4f4,#e2e2e2)}
.col{top:40px;width:300px;text-align:center}
.col svg{display:block;margin:0 auto}
.col h3{margin-top:26px;font-size:18px;color:var(--ink)}
.col p{margin-top:12px;font-size:12.5px;line-height:24px;color:var(--grey)}
.col .btn{position:relative;margin:28px auto 0;width:115px;height:40px;font-size:12px;border-width:2px;border-color:var(--grey);color:var(--ink)}

/* ministries */
.ministry{top:1985px;height:366px;background:var(--indigo)}
.tile{position:absolute;overflow:hidden}
.tile .label{position:absolute;bottom:12px;left:50%;transform:translateX(-50%);background:var(--indigo);color:var(--white);font-family:"Montserrat",Arial,sans-serif;font-weight:600;font-size:11px;padding:5px 16px;text-transform:uppercase;white-space:nowrap}

/* blog */
.blog{top:2351px;height:352px;background:#e4e4e4}
.blog-side{left:0;top:0;width:447px;height:352px;background:var(--indigo)}

/* podcast */
.podcast{top:2703px;height:447px;background:linear-gradient(90deg,#161616,#262626 55%,#1a1a1a)}
.play{left:736px;width:49px;height:49px;border:1.5px solid rgba(255,255,255,.6);display:flex;align-items:center;justify-content:center}
.track{left:808px;color:var(--white);font-family:"Montserrat",Arial,sans-serif;font-size:14px;line-height:26px}

/* events */
.events{top:3150px;height:825px;background:var(--white)}
.date{left:159px;width:83px;height:86px;background:var(--indigo);color:var(--white);text-align:center}
.date b{display:block;font-family:"Montserrat",Arial,sans-serif;font-size:30px;padding-top:12px}
.date span{font-size:12px;text-transform:uppercase}
.ev-title{left:511px;width:340px;font-family:"Montserrat",Arial,sans-serif;font-weight:700;font-size:15px;line-height:27px;color:var(--ink);text-transform:uppercase}
.meta{left:511px;font-size:13px;color:var(--grey);display:flex;align-items:center;gap:12px}
.meta svg{flex:none}
.vline{left:857px;width:1px;height:170px;background:#dcdcdc}

/* footer */
.site-footer{top:3975px;height:352px;background:var(--ink);color:var(--white)}
.fh{top:46px;font-size:18px}
.thumb{width:80px;height:58px}
.ftext{font-size:12.5px;line-height:26px;color:#d8d8d8}
.tag{position:absolute;height:32px;border:1px solid #888;font-size:12px;display:flex;align-items:center;justify-content:center;color:var(--white)}
</style>
</head>
<body>

<header class="hero">
  <div class="ph" role="img" aria-label="Photo of a church spire against a sunset sky"></div>
  <nav class="nav">
    <a style="left:193px">Home</a><a style="left:307px">Team</a><a style="left:416px">Features</a><a style="left:557px">Events</a><a style="left:680px">Sermons</a><a style="left:817px">Contact Us</a><a style="left:972px">Blog</a>
  </nav>
  <div class="abs brand"><span class="dot"></span>Wellspring</div>
  <div class="btn btn-ghost worship">Sunday Worship 10:15</div>
  <h1 class="abs hero-title head" style="top:312px;font-size:40px;font-weight:600">Wellspring of</h1>
  <h1 class="abs hero-title head" style="top:368px;font-size:70px;font-weight:600">Grace Church</h1>
  <p class="abs hero-sub">Sed ut perspiciatis unde omnis iste natus error sit volup<br>cusantium doloremque laudantium</p>
  <div class="btn btn-solid" style="left:513px;top:565px;width:174px;height:47px">Read More</div>
</header>

<section class="band">
  <p class="abs">Sed ut perspiciatis unde omnis iste natus error sit voluptatem</p>
  <div class="btn btn-ghost" style="left:851px;top:13px;width:156px;height:44px">Visiter Info</div>
</section>

<section class="welcome">
  <p class="abs head" style="left:110px;top:50px;font-size:17px;font-weight:500;color:var(--ink)">Welcome to</p>
  <h2 class="abs head" style="left:110px;top:82px;font-size:29px;font-weight:600;color:var(--indigo)">Wellspring of Grace Church</h2>
  <p class="abs copy" style="left:110px;top:142px;width:530px;font-size:12.5px">Sed ut perspiciatis unde omnis iste natus error sit voluptatem accusantium doloremque laudantium, totam rem aperiam, eaque ipsa quae ab illo inventore veritatis et quasi architecto beatae vitae dicta sunt explicabo. Nemo enim ipsam voluptatem quia voluptas sit aspernatur aut odit aut fugit, sed quia consequuntur magni dolores eos qui ratione voluptatem sequi nesciunt. Neque porro quisquam est, qui dolorem ipsum quia dolor sit amet, consectetur, adipisci velit, sed quia non numquam eius modi tempora incidunt ut labore et dolore</p>
  <p class="abs copy" style="left:110px;top:322px;width:530px;font-size:12.5px">Neque porro quisquam est, qui dolorem ipsum quia dolor sit amet, consectetur, adipisci velit, sed quia non numquam eius modi tempora incidunt ut labore et dolore magnam aliquam quaerat volup tatem. Ut enim ad minima veniam quis nostrum exercitationem ullam.</p>
  <p class="abs signature">by Aaron Miles</p>
  <div class="ph" role="img" aria-label="Photo of two church leaders holding bibles"></div>
</section>

<section class="meeting">
  <div class="ph" style="inset:0;background:linear-gradient(90deg,rgba(0,0,0,.25),rgba(0,0,0,.1))" role="img" aria-label="Dim photo of a church interior"></div>
  <h3 class="abs head" style="left:140px;top:72px;width:400px;text-align:center;font-size:19px;font-weight:600;color:var(--white)">Church Leaders Meeting</h3>
  <p class="abs" style="left:140px;top:108px;width:400px;text-align:center;font-size:12px;color:#bbb;text-transform:uppercase">March 27, 2019 7:00PM</p>
  <p class="abs" style="left:140px;top:145px;width:400px;text-align:center;font-size:12.5px;line-height:26px;color:var(--white)">Meeting for the Church leaders.This is where we plan the Strategy<br>for the Church and give feedback on projects</p>
  <div class="abs count" style="left:644px"><b>80</b><span>days</span></div>
  <div class="abs sep" style="left:728px"></div>
  <div class="abs count" style="left:733px"><b>05</b><span>hours</span></div>
  <div class="abs sep" style="left:819px"></div>
  <div class="abs count" style="left:826px"><b>05</b><span>minutes</span></div>
  <div class="abs sep" style="left:911px"></div>
  <div class="abs count" style="left:915px"><b>20</b><span>seconds</span></div>
  <div class="btn btn-solid" style="left:756px;top:175px;width:127px;height:46px;font-size:13px">Read More</div>
</section>

<section class="beliefs">
  <div class="abs col" style="left:115px">
    <svg width="90" height="90" viewBox="0 0 90 90" fill="none" stroke="var(--royal)" stroke-width="3" stroke-linejoin="round"><path d="M45 80 C20 60 6 45 6 28 A18 18 0 0 1 45 20 A18 18 0 0 1 84 28 C84 45 70 60 45 80Z"/><path d="M14 44 H32 L38 32 L46 56 L52 40 L56 44 H76"/></svg>
    <h3 class="head">What we believe?</h3>
    <p>Sed ut perspiciatis unde omnis iste natus error sit voluptatem accusantium doloremque laudantium, beatae vitae dicta sunt explicabo.</p>
    <div class="btn btn-line">Read More</div>
  </div>
  <div class="abs col" style="left:456px">
    <svg width="90" height="90" viewBox="0 0 90 90" fill="none" stroke="var(--royal)" stroke-width="3" stroke-linejoin="round"><path d="M6 30 L28 22 L50 30 L84 20 V76 L50 84 L28 76 L6 84Z"/><path d="M28 22 V76 M50 30 V84"/><path d="M62 46 C52 32 52 22 62 14 C72 22 72 32 62 46Z" fill="var(--white)"/><circle cx="62" cy="24" r="4"/></svg>
    <h3 class="head">Services &amp; Location</h3>
    <p>Sed ut perspiciatis unde omnis iste natus error sit voluptatem accusantium doloremque laudantium, beatae vitae dicta sunt explicabo.</p>
    <div class="btn btn-line">Read More</div>
  </div>
  <div class="abs col" style="left:785px">
    <svg width="90" height="90" viewBox="0 0 90 90" fill="none" stroke="var(--royal)" stroke-width="3" stroke-linejoin="round"><path d="M52 40 C40 30 34 24 34 16 A9 9 0 0 1 52 12 A9 9 0 0 1 70 16 C70 24 64 30 52 40Z"/><path d="M6 62 L22 54 C30 50 38 52 46 56 H60 A5 5 0 0 1 60 66 H42 M60 66 L78 56 A5 5 0 0 1 84 64 L58 80 H30 L16 86"/></svg>
    <h3 class="head">Giving</h3>
    <p>Sed ut perspiciatis unde omnis iste natus error sit voluptatem accusantium doloremque laudantium, beatae vitae dicta sunt explicabo.</p>
    <div class="btn btn-line">Read More</div>
  </div>
</section>

<section class="ministry">
  <div class="tile" style="left:0;top:0;width:381px;height:182px;background:linear-gradient(135deg,#6a4a3a,#2e3a5a)" role="img" aria-label="Photo of children at a kids ministry class"><span class="label">Kids Ministry</span></div>
  <div class="tile" style="left:387px;top:0;width:184px;height:182px;background:linear-gradient(135deg,#8a7a6a,#4a4038)" role="img" aria-label="Photo of seniors reading together"><span class="label">Seniors Ministry</span></div>
  <div class="tile" style="left:577px;top:0;width:188px;height:182px;background:linear-gradient(135deg,#5a4a40,#2a2420)" role="img" aria-label="Photo of hands on an open bible"><span class="label">Bible Study</span></div>
  <div class="tile" style="left:0;top:186px;width:188px;height:180px;background:linear-gradient(135deg,#5a3a2a,#2a3a6a)" role="img" aria-label="Photo of teenagers smiling"><span class="label">Teens Ministry</span></div>
  <div class="tile" style="left:193px;top:186px;width:188px;height:180px;background:linear-gradient(135deg,#8aa0b0,#7a8a4a)" role="img" aria-label="Photo of children playing outdoors"><span class="label">Kids Ministry</span></div>
  <div class="tile" style="left:387px;top:186px;width:378px;height:180px;background:linear-gradient(135deg,#9a9088,#5a5048)" role="img" aria-label="Photo of volunteers holding hands in a circle"><span class="label">Outreach Ministry</span></div>
  <h2 class="abs head" style="left:765px;top:106px;width:435px;text-align:center;font-size:30px;font-weight:600;color:var(--white)">Get Involved</h2>
  <p class="abs copy" style="left:805px;top:160px;width:355px;text-align:center;font-size:12.5px;color:var(--white)">Sed ut perspiciatis unde omnis iste natus error sit voluptatem accusantium doloremque laudantium, totam rem aperiam, eaque ipsa quae ab illo inventore veritatis et quasi architecto beatae vitae dicta sunt explicabo.</p>
</section>

<section class="blog">
  <div class="abs blog-side" role="img" aria-label="Deep indigo background"></div>
  <h2 class="abs head" style="left:0;top:42px;width:447px;text-align:center;font-size:30px;font-weight:600;color:var(--white)">Latest Blog</h2>
  <p class="abs" style="left:0;top:88px;width:447px;text-align:center;font-size:14px;color:#ddd;text-transform:uppercase">April 14, 2019</p>
  <p class="abs copy" style="left:62px;top:128px;width:323px;text-align:center;font-size:12.5px;color:var(--white)">Sed ut perspiciatis unde omnis iste natus error sit voluptatem accusantium doloremque laudantium, totam rem aperiam, eaque ipsa quae ab illo inventore veritatis et quasi architecto beatae vitae dicta sunt explicabo.</p>
  <div class="btn btn-solid" style="left:159px;top:257px;width:132px;height:43px">Read More</div>
  <h2 class="abs head" style="left:519px;top:55px;font-size:29px;font-weight:600;color:var(--charcoal)">Pray Without Ceasing</h2>
  <p class="abs copy" style="left:519px;top:112px;width:560px;font-size:12.5px">Sed ut perspiciatis unde omnis iste natus error sit voluptatem accusantium doloremque laudantium, totam rem aperiam, eaque ipsa quae ab illo inventore veritatis et quasi architecto beatae vitae dicta sunt explicabo. Nemo enim ipsam voluptatem quia voluptas sit aspernatur aut odit aut fugit, sed quia consequuntur magni dolores eos qui ratione voluptatem sequi nesciunt. Neque porro quisquam est, qui dolorem ipsum quia dolor sit amet, consectetur, adipisci velit.</p>
  <div class="btn btn-solid" style="left:519px;top:266px;width:145px;height:43px">Read More</div>
</section>

<section class="podcast">
  <div class="ph" style="left:110px;top:75px;width:228px;height:280px;background:linear-gradient(135deg,#8a6a58,#3a2a22)" role="img" aria-label="Photo of a pastor holding an open bible"></div>
  <h3 class="abs head" style="left:366px;top:88px;font-size:20px;font-weight:600;color:var(--white)">One thing I ask of the Load</h3>
  <p class="abs copy" style="left:366px;top:138px;width:340px;font-size:12px;line-height:26px;color:#cfcfcf">Sed ut perspiciatis unde omnis iste natus error sit voluptatem accu santium doloremque laudantium, totam rem aperiam, eaque ipsa quae ab illo inventore veritatis et quasi architecto beatae vitae dicta sunt explicabo. Nemo enim ipsam voluptatem quia voluptas sit aspernatur aut odit aut fugit, sed quia consequuntur magni dolores eos qui ratione voluptatem sequi nesciunt neque porro quisquam est qui dolorem ipsum quia dolor sit amet consectetur magni dolores eos</p>
  <p class="abs" style="left:736px;top:52px;font-family:'Montserrat',Arial,sans-serif;font-size:22px;color:var(--white);text-transform:uppercase">Podcast</p>
  <div class="abs play" style="top:95px"><svg width="16" height="18" viewBox="0 0 16 18"><path d="M2 1 L15 9 L2 17Z" fill="#ccc"/></svg></div>
  <p class="abs track" style="top:94px">HOLY SPIRIT : STRATEGIC THINKING<br>by : Aaron Miles</p>
  <div class="abs play" style="top:202px"><svg width="16" height="18" viewBox="0 0 16 18"><path d="M2 1 L15 9 L2 17Z" fill="#ccc"/></svg></div>
  <p class="abs track" style="top:201px">HOLY SPIRIT : STRATEGIC THINKING<br>by : Aaron Miles</p>
  <div class="abs play" style="top:308px"><svg width="16" height="18" viewBox="0 0 16 18"><path d="M2 1 L15 9 L2 17Z" fill="#ccc"/></svg></div>
  <p class="abs track" style="top:307px">HOLY SPIRIT : STRATEGIC THINKING<br>by : Aaron Miles</p>
</section>

<section class="events">
  <h2 class="abs head" style="left:0;top:38px;width:1200px;text-align:center;font-size:30px;font-weight:600;color:var(--ink)">Upcoming Events</h2>
  <p class="abs" style="left:0;top:86px;width:1200px;text-align:center;font-size:12.5px">Sed ut perspiciatis unde omnis iste natus error sit voluptatem accusantium doloremque laudantium.</p>

  <div class="abs date" style="top:168px"><b>22</b><span>Apr 2019</span></div>
  <div class="ph" style="left:251px;top:168px;width:231px;height:173px;background:linear-gradient(135deg,#f0c070,#7a4a2a)" role="img" aria-label="Photo of a cross in warm light"></div>
  <p class="abs ev-title" style="top:166px">Sed ut perspiciatis unde omnis iste natus voluptatem accusantium</p>
  <p class="abs meta" style="top:240px"><svg width="14" height="14" viewBox="0 0 14 14" fill="none" stroke="var(--royal)" stroke-width="1.6"><rect x="1" y="2.5" width="12" height="10.5"/><path d="M1 6 H13 M4 1 V4 M10 1 V4"/></svg>Thursday,09.00 am - Thursday, 09.00 am</p>
  <p class="abs meta" style="top:281px;color:var(--royal)"><svg width="14" height="14" viewBox="0 0 14 14"><path d="M7 13 C3 8 2 6 2 5 A5 5 0 0 1 12 5 C12 6 11 8 7 13Z" fill="var(--royal)"/><circle cx="7" cy="5" r="1.8" fill="#fff"/></svg>St Harbor Chapel</p>
  <p class="abs meta" style="top:315px"><svg width="14" height="14" viewBox="0 0 14 14"><path d="M1 13 C1 7 5 5 9 5 V1 L13 6 L9 11 V8 C5 8 3 9 1 13Z" fill="var(--royal)"/></svg>Elm Row, Newtown, Statesville, 10452</p>
  <div class="abs vline" style="top:170px"></div>
  <div class="btn btn-line" style="left:891px;top:220px;width:150px;height:49px">Read More</div>

  <div class="abs date" style="top:379px"><b>22</b><span>Apr 2019</span></div>
  <div class="ph" style="left:251px;top:379px;width:231px;height:173px;background:linear-gradient(135deg,#e8dcc8,#6a5a8a)" role="img" aria-label="Photo of a congregation raising hands in worship"></div>
  <p class="abs ev-title" style="top:377px">Sed ut perspiciatis unde omnis iste natus voluptatem accusantium</p>
  <p class="abs meta" style="top:451px"><svg width="14" height="14" viewBox="0 0 14 14" fill="none" stroke="var(--royal)" stroke-width="1.6"><rect x="1" y="2.5" width="12" height="10.5"/><path d="M1 6 H13 M4 1 V4 M10 1 V4"/></svg>Thursday,09.00 am - Thursday, 09.00 am</p>
  <p class="abs meta" style="top:492px;color:var(--royal)"><svg width="14" height="14" viewBox="0 0 14 14"><path d="M7 13 C3 8 2 6 2 5 A5 5 0 0 1 12 5 C12 6 11 8 7 13Z" fill="var(--royal)"/><circle cx="7" cy="5" r="1.8" fill="#fff"/></svg>St Harbor Chapel</p>
  <p class="abs meta" style="top:526px"><svg width="14" height="14" viewBox="0 0 14 14"><path d="M1 13 C1 7 5 5 9 5 V1 L13 6 L9 11 V8 C5 8 3 9 1 13Z" fill="var(--royal)"/></svg>Elm Row, Newtown, Statesville, 10452</p>
  <div class="abs vline" style="top:381px"></div>
  <div class="btn btn-line" style="left:891px;top:431px;width:150px;height:49px">Read More</div>

  <div class="abs date" style="top:589px"><b>22</b><span>Apr 2019</span></div>
  <div class="ph" style="left:251px;top:589px;width:231px;height:173px;background:linear-gradient(135deg,#f0a060,#6a2a2a)" role="img" aria-label="Photo of worshippers gathered at a service"></div>
  <p class="abs ev-title" style="top:587px">Sed ut perspiciatis unde omnis iste natus voluptatem accusantium</p>
  <p class="abs meta" style="top:661px"><svg width="14" height="14" viewBox="0 0 14 14" fill="none" stroke="var(--royal)" stroke-width="1.6"><rect x="1" y="2.5" width="12" height="10.5"/><path d="M1 6 H13 M4 1 V4 M10 1 V4"/></svg>Thursday,09.00 am - Thursday, 09.00 am</p>
  <p class="abs meta" style="top:702px;color:var(--royal)"><svg width="14" height="14" viewBox="0 0 14 14"><path d="M7 13 C3 8 2 6 2 5 A5 5 0 0 1 12 5 C12 6 11 8 7 13Z" fill="var(--royal)"/><circle cx="7" cy="5" r="1.8" fill="#fff"/></svg>St Harbor Chapel</p>
  <p class="abs meta" style="top:736px"><svg width="14" height="14" viewBox="0 0 14 14"><path d="M1 13 C1 7 5 5 9 5 V1 L13 6 L9 11 V8 C5 8 3 9 1 13Z" fill="var(--royal)"/></svg>Elm Row, Newtown, Statesville, 10452</p>
  <div class="abs vline" style="top:591px"></div>
  <div class="btn btn-line" style="left:891px;top:641px;width:150px;height:49px">Read More</div>
</section>

<footer class="site-footer">
  <h4 class="abs head fh" style="left:113px">Latest Sermons</h4>
  <div class="ph thumb" style="left:113px;top:99px;background:linear-gradient(135deg,#c08a6a,#5a3a2a)" role="img" aria-label="Sermon thumbnail photo"></div>
  <p class="abs ftext" style="left:211px;top:100px;width:240px">Sed ut perspiciatis unde omnis iste natus error sit voluptatem accusantium...</p>
  <div class="ph thumb" style="left:113px;top:197px;background:linear-gradient(135deg,#e0905a,#6a2a2a)" role="img" aria-label="Sermon thumbnail photo"></div>
  <p class="abs ftext" style="left:211px;top:198px;width:240px">Sed ut perspiciatis unde omnis iste natus error sit voluptatem accusantium...</p>

  <h4 class="abs head fh" style="left:490px">Sermon Tag</h4>
  <div class="tag" style="left:485px;top:92px;width:128px">Sed ut perspiciatis</div>
  <div class="tag" style="left:620px;top:92px;width:92px">perspiciatis</div>
  <div class="tag" style="left:485px;top:135px;width:62px">Lorem</div>
  <div class="tag" style="left:555px;top:135px;width:92px">perspiciatis</div>
  <div class="tag" style="left:655px;top:135px;width:62px">Lorem</div>
  <div class="tag" style="left:485px;top:178px;width:128px">Sed ut perspiciatis</div>
  <div class="tag" style="left:620px;top:178px;width:92px">perspiciatis</div>

  <h4 class="abs head fh" style="left:773px">Latest News</h4>
  <div class="ph thumb" style="left:773px;top:99px;background:linear-gradient(135deg,#b07a60,#4a2a22)" role="img" aria-label="News thumbnail photo"></div>
  <p class="abs ftext" style="left:870px;top:100px;width:240px">Sed ut perspiciatis unde omnis iste natus error sit voluptatem accusantium...</p>
  <div class="ph thumb" style="left:773px;top:197px;background:linear-gradient(135deg,#e0a070,#7a3a2a)" role="img" aria-label="News thumbnail photo"></div>
  <p class="abs ftext" style="left:870px;top:198px;width:240px">Sed ut perspiciatis unde omnis iste natus error sit voluptatem accusantium...</p>

  <p class="abs" style="left:0;top:306px;width:1200px;text-align:center;font-size:12.5px;color:#ddd">© Copyright-2019 Wellspring of Grace Church . All rights reserved.</p>
</footer>

</body>
</html>
```